Telecommunications/Power civil contractor needs business card design

Were a new telecommunications/power underground civil contractor that is looking for a new business card design. Our company colours are silver or grey and orange. Feel free to use the white background logo or the black background logo.

Target Market(s)

Local contractors, utility companies, private sector mining/energy companies, developers.

Industry/Entity Type

Telecommunications

Contact Information for Business Card

Each card will need the following info:
Persons name:
Title:
E-mail:
Phone number:
Shop Address:
Mailing Address:

Requirements
Must have
• Each card will need the following info:
• Persons name:
• Title:
• E-mail:
• Phone number:
• Shop Address:
• Mailing Address:

```html
<!DOCTYPE html>
<html lang="en">
<head>
<meta charset="utf-8">
<title>Dig Line Contracting Inc – Business Card</title>
<link href="https://fonts.googleapis.com/css2?family=Arimo:wght@400;700&display=swap" rel="stylesheet">
<style>
  :root {
    --backdrop: #2b2b2b;
    --card-white: #f7f7f7;
    --brand-orange: #e2531b;
    --brand-grey: #5b5b5b;
    --brand-silver: #a7a7a7;
    --ink: #1e1e1e;
  }
  * { box-sizing: border-box; margin: 0; padding: 0; }
  html, body {
    width: 1200px;
    height: 997px;
    overflow: hidden;
    background: var(--backdrop);
    font-family: "Arimo", Arial, sans-serif;
  }
  .card {
    position: absolute;
    left: 170px;
    top: 252px;
    width: 860px;
    height: 492px;
    background: var(--card-white);
    border-radius: 22px;
    overflow: hidden;
  }
  .card__stripe {
    position: absolute;
    left: 0;
    right: 0;
    bottom: 0;
    height: 16px;
    background: linear-gradient(var(--brand-orange) 0 6px, var(--brand-grey) 6px 100%);
  }
  .brand {
    position: absolute;
    top: 50px;
    left: 0;
    right: 0;
    display: flex;
    flex-direction: column;
    align-items: center;
    gap: 14px;
  }
  .brand__dot {
    width: 86px;
    height: 86px;
    border-radius: 50%;
    background: var(--brand-grey);
  }
  .brand__name {
    font-weight: 700;
    font-size: 30px;
    letter-spacing: 1px;
    color: var(--brand-orange);
    text-transform: uppercase;
  }
  .contact {
    position: absolute;
    right: 46px;
    top: 214px;
    list-style: none;
    display: flex;
    flex-direction: column;
    align-items: flex-end;
    gap: 13px;
    font-size: 19px;
    color: var(--ink);
  }
  .contact__item {
    display: flex;
    align-items: center;
    gap: 14px;
  }
  .contact__item--address {
    color: var(--brand-grey);
    font-size: 17px;
  }
  .contact__label {
    font-weight: 700;
    color: var(--brand-orange);
    margin-right: 6px;
  }
  .contact__icon {
    width: 18px;
    height: 18px;
    flex: none;
  }
  .contact__divider {
    width: 300px;
    height: 1px;
    background: var(--brand-silver);
  }
  .person {
    position: absolute;
    left: 60px;
    bottom: 70px;
  }
  .person__name {
    font-weight: 700;
    font-size: 24px;
    color: var(--brand-grey);
  }
  .person__title {
    margin-top: 4px;
    font-size: 19px;
    color: var(--brand-orange);
  }
</style>
</head>
<body>
  <div class="card">
    <div class="brand">
      <div class="brand__dot"></div>
      <div class="brand__name">Dig Line Contracting Inc</div>
    </div>

    <ul class="contact">
      <li class="contact__item">
        <span>5550142873</span>
        <svg class="contact__icon" viewBox="0 0 18 18" aria-hidden="true">
          <path d="M4 2h3l1.5 4-2 1.3a9 9 0 0 0 4.2 4.2L12 9.5l4 1.5v3a2 2 0 0 1-2 2A12 12 0 0 1 2 4a2 2 0 0 1 2-2z" fill="var(--brand-orange)"/>
        </svg>
      </li>
      <li class="contact__item">
        <span>info@diglinecontracting.com</span>
        <svg class="contact__icon" viewBox="0 0 18 18" aria-hidden="true">
          <rect x="1" y="4" width="16" height="11" rx="1.5" fill="var(--brand-orange)"/>
          <path d="M1.5 4.8 9 10l7.5-5.2" fill="none" stroke="#fff" stroke-width="1.3"/>
        </svg>
      </li>
      <li class="contact__item">
        <span>www.diglinecontracting.com</span>
        <svg class="contact__icon" viewBox="0 0 18 18" aria-hidden="true">
          <circle cx="9" cy="9" r="8" fill="var(--brand-orange)"/>
          <path d="M1 9h16M9 1c3 3 3 13 0 16M9 1c-3 3-3 13 0 16" fill="none" stroke="#fff" stroke-width="1"/>
        </svg>
      </li>
      <li class="contact__divider" aria-hidden="true"></li>
      <li class="contact__item contact__item--address">
        <span><span class="contact__label">Shop</span>48 Quarry Road, Millbrook, AB T4X 2K9</span>
        <svg class="contact__icon" viewBox="0 0 18 18" aria-hidden="true">
          <path d="M9 1a6 6 0 0 0-6 6c0 4.5 6 10 6 10s6-5.5 6-10a6 6 0 0 0-6-6z" fill="var(--brand-grey)"/>
          <circle cx="9" cy="7" r="2.2" fill="#fff"/>
        </svg>
      </li>
      <li class="contact__item contact__item--address">
        <span><span class="contact__label">Mail</span>PO Box 317, Millbrook, AB T4X 0C1</span>
        <svg class="contact__icon" viewBox="0 0 18 18" aria-hidden="true">
          <rect x="1" y="4" width="16" height="11" rx="1.5" fill="var(--brand-grey)"/>
          <path d="M1.5 4.8 9 10l7.5-5.2" fill="none" stroke="#fff" stroke-width="1.3"/>
        </svg>
      </li>
    </ul>

    <div class="person">
      <div class="person__name">Daniel Marsh</div>
      <div class="person__title">Chairman</div>
    </div>

    <div class="card__stripe"></div>
  </div>
</body>
</html>
```